Website Design for The Elder Nook

Please design and code a new website.
Here are the sites I like best:
http://www.voyaglint.com/alternate/
http://www.wheelgiftbay.org
Please make it similar but look at the competitor site (below) for images and wording. This is NOT a car donation site. It's a senior lead placement site like https://www.kinhavenfinder.com. I just like this sites above as a lead generation sites.
Competitor site:
https://www.kinhavenfinder.com (use ideas / verbiage from this site)
Updates
Competitor site:
Coding
Coded - Design and coding required
Number of Pages Required
1 page
Look and feel
Each slider illustrates characteristics of the customer's brand and the style your logo design should communicate.

```html
<!DOCTYPE html>
<html lang="en">
<head>
<meta charset="utf-8">
<title>The Elder Nook — Senior Living</title>
<link href="https://fonts.googleapis.com/css2?family=Poppins:wght@600;700;800&family=Open+Sans:wght@400;600;700&display=swap" rel="stylesheet">
<style>
:root{
  --blue:#1b5dab;
  --blue-dark:#174f94;
  --orange:#f05a24;
  --ink:#3a3a3a;
  --muted:#555;
  --page-bg:#f0efed;
  --soft:#f2f1ef;
  --card:#efeeec;
  --white:#fff;
}
*{margin:0;padding:0;box-sizing:border-box}
html,body{width:1200px;height:2799px;overflow:hidden;background:var(--page-bg)}
body{font-family:'Open Sans',sans-serif;color:var(--ink)}
.page{position:absolute;left:218px;top:0;width:764px;height:2799px;background:var(--white)}
section,header,footer,nav{position:absolute;left:0;width:764px}
.abs{position:absolute}
.heading{font-family:'Poppins',sans-serif;font-weight:700}

/* header */
.site-header{top:0;height:81px;background:var(--white)}
.brand{left:34px;top:18px;font-size:30px;color:var(--blue);font-weight:400}
.call{left:551px;top:20px}
.call-label{left:590px;top:20px;font-size:12px;font-weight:700;color:var(--ink)}
.call-number{left:590px;top:33px;font-family:'Poppins',sans-serif;font-weight:700;font-size:24px;color:var(--blue)}

.main-nav{top:81px;height:35px;background:var(--blue);display:flex;justify-content:space-around;align-items:center;padding:0 10px}
.main-nav a{color:var(--white);font-size:11px;font-weight:700;text-decoration:none;text-transform:uppercase}

/* hero */
.hero{top:116px;height:396px;background:linear-gradient(100deg,#6b4a2c 0%,#a87444 35%,#c99a6c 55%,#d9cfc4 75%,#8d7a68 100%)}
.hero-title{left:51px;top:66px;font-size:30px;font-weight:800;line-height:37px;color:var(--white)}
.hero-sub{left:53px;top:164px;font-size:15px;color:var(--white)}
.search-input{background:var(--white);display:flex;align-items:center;gap:10px;padding-left:20px;font-size:12px;font-weight:700;color:var(--ink)}
.hero .search-input{left:56px;top:197px;width:347px;height:48px}
.btn{background:var(--orange);color:var(--white);font-family:'Poppins',sans-serif;font-weight:700;text-transform:uppercase;display:flex;align-items:center;justify-content:center}
.hero .btn{left:56px;top:271px;width:127px;height:43px;font-size:15px}

/* support */
.support{top:512px;height:300px;text-align:center}
.support h2{position:absolute;top:32px;width:100%;font-size:20px;color:var(--ink)}
.support h2 b{font-weight:800}
.support p{position:absolute;top:66px;width:100%;font-size:13px;color:var(--muted)}
.feature{top:118px;width:140px;height:155px;background:var(--card);text-align:center}
.feature svg{position:absolute;left:40px;top:24px}
.feature span{position:absolute;top:96px;left:0;width:100%;font-size:10px;font-weight:700;line-height:15px;text-transform:uppercase;color:var(--ink)}

/* advisor */
.advisor{top:812px;height:398px;background:linear-gradient(90deg,#4f4a2d 0%,#7d7a53 30%,#9a9272 45%,#6b6a4c 65%,#54532f 100%)}
.advisor h2{left:377px;top:32px;font-size:20px;line-height:24px;color:var(--white)}
.advisor .lead{left:381px;top:84px;font-size:13.5px;font-weight:700;line-height:19px;color:var(--white);width:300px}
.perk{left:382px;display:flex;align-items:center;gap:18px;color:var(--white);font-size:13px;font-weight:700;line-height:16px;text-transform:uppercase}
.advisor .search-input{left:390px;top:329px;width:227px;height:45px;font-size:11px}
.advisor .btn{left:617px;top:329px;width:86px;height:45px;font-size:15px}

/* testimonials */
.testimonials{top:1210px;height:486px;background:var(--soft);text-align:center}
.testimonials h2{position:absolute;top:42px;width:100%;font-size:28px;color:var(--ink)}
.review{top:119px;width:220px;margin-left:-110px}
.portrait{width:156px;height:156px;border-radius:50%;margin:0 auto;background:radial-gradient(circle at 50% 45%,#b9a79a 0%,#6c6a5c 55%,#3c4a3a 100%)}
.review q{display:block;margin-top:20px;font-size:11px;font-weight:700;line-height:15px;text-transform:uppercase;quotes:"\201C" "\201D"}
.review p{margin-top:9px;font-size:10px;line-height:13.5px;color:var(--muted)}
.testimonials .btn{left:275px;top:409px;width:214px;height:38px;font-size:14px}

/* veterans */
.veterans{top:1696px;height:345px;background:linear-gradient(90deg,#7d2a2e 0%,#b04045 25%,#33507e 45%,#2d4a7a 55%,#9c4346 75%,#8a3a3e 100%)}
.veterans h2{left:464px;top:50px;font-size:25px;line-height:30.5px;text-transform:uppercase;color:var(--white)}
.veterans p{left:465px;top:161px;width:270px;font-size:16px;font-weight:700;line-height:18px;color:var(--white)}
.veterans .btn{left:466px;top:254px;width:128px;height:38px;font-size:14px}

/* states */
.states{top:2041px;height:482px}
.states h2{position:absolute;top:42px;width:100%;text-align:center;font-size:28px;color:var(--ink)}
.tabs{left:24px;top:118px;display:flex;height:36px}
.tabs span{padding:0 15px;font-size:11px;font-weight:700;display:flex;align-items:center;text-transform:uppercase;color:var(--ink)}
.tabs .active{background:var(--soft)}
.panel{left:24px;top:154px;width:720px;height:304px;background:var(--soft)}
.panel ul{position:absolute;top:36px;list-style:none;font-size:12px;line-height:17.4px;color:var(--muted)}

/* footer */
.site-footer{top:2523px;height:226px;background:var(--blue)}
.footer-brand{left:52px;top:67px;font-size:30px;color:var(--white)}
.follow{left:58px;top:137px;font-size:12px;font-weight:700;color:var(--white)}
.social{top:132px;width:25px;height:25px;border-radius:50%}
.footer-col h3{font-family:'Poppins',sans-serif;font-size:13px;font-weight:700;color:var(--white);text-transform:uppercase;padding-bottom:3px;border-bottom:2px solid var(--white);display:inline-block}
.footer-col p,.footer-col li{font-size:12px;line-height:16px;color:var(--white);list-style:none}
.about{left:312px;top:44px;width:225px}
.about p{margin-top:20px}
.menu{left:599px;top:44px}
.menu ul{margin-top:20px;text-transform:uppercase}
.legal{top:2749px;height:50px;background:var(--blue-dark);text-align:center;font-size:9px;line-height:50px;color:var(--white)}
</style>
</head>
<body>
<div class="page">

<header class="site-header">
  <div class="abs brand">The Elder Nook</div>
  <svg class="abs call" width="28" height="28" viewBox="0 0 24 24" fill="none" stroke="#1b5dab" stroke-width="1.6" aria-hidden="true"><path d="M5 3h4l2 5-2.5 1.5a11 11 0 0 0 6 6L16 13l5 2v4a2 2 0 0 1-2 2A17 17 0 0 1 3 5a2 2 0 0 1 2-2z"/><path d="M14 3a7 7 0 0 1 7 7M14 6.5a3.5 3.5 0 0 1 3.5 3.5"/></svg>
  <div class="abs call-label">CALL US NOW</div>
  <div class="abs call-number">888.888.8888</div>
</header>

<nav class="main-nav">
  <a href="#">Assisted Living</a><a href="#">Memory Care</a><a href="#">Nursing Homes</a><a href="#">Planning &amp; Advice</a><a href="#">How It Works</a><a href="#">Contact Us</a>
</nav>

<section class="hero" role="img" aria-label="Smiling older man with glasses and white beard in a warm indoor setting">
  <h1 class="abs heading hero-title">You know your family.<br>We know SENIOR LIVING.</h1>
  <div class="abs hero-sub">Find Senior Living Near You.</div>
  <div class="abs search-input"><svg width="9" height="12" viewBox="0 0 10 14"><path d="M5 0a5 5 0 0 0-5 5c0 4 5 9 5 9s5-5 5-9a5 5 0 0 0-5-5zm0 7a2 2 0 1 1 0-4 2 2 0 0 1 0 4z" fill="#3a3a3a"/></svg>ENTER CITY OR POSTAL CODE</div>
  <div class="abs btn">Search</div>
</section>

<section class="support">
  <h2 class="heading">The support you need to make the <b>RIGHT CHOICE</b></h2>
  <p>Lorem Ipsum is simply dummy text of the printing and typesetting industry</p>
  <div class="abs feature" style="left:13px"><svg width="60" height="60" viewBox="0 0 60 60" fill="#8a8a8a"><circle cx="30" cy="16" r="11"/><path d="M10 56c0-14 8-22 20-22s20 8 20 22z"/></svg><span>Dedicated<br>local advisor</span></div>
  <div class="abs feature" style="left:162px"><svg width="60" height="60" viewBox="0 0 60 60" fill="#8a8a8a"><path d="M4 28L30 8l26 20v4H4z"/><rect x="9" y="32" width="42" height="22"/><rect x="15" y="37" width="8" height="7" fill="#efeeec"/><rect x="28" y="37" width="8" height="7" fill="#efeeec"/><rect x="41" y="39" width="6" height="15" fill="#efeeec"/></svg><span>Hand-picked list<br>of communities to<br>match your needs</span></div>
  <div class="abs feature" style="left:311px"><svg width="60" height="60" viewBox="0 0 60 60" fill="#8a8a8a"><circle cx="32" cy="14" r="11"/><text x="32" y="19" font-size="14" text-anchor="middle" fill="#efeeec" font-family="Open Sans,sans-serif" font-weight="700">$</text><path d="M6 40l10-6h14a3 3 0 0 1 0 6H22h10l14-8a3 3 0 0 1 4 4L34 50H16l-6 4z"/></svg><span>Full details<br>and pricing</span></div>
  <div class="abs feature" style="left:460px"><svg width="60" height="60" viewBox="0 0 60 60" fill="none" stroke="#8a8a8a" stroke-width="4"><rect x="9" y="12" width="42" height="40"/><path d="M9 22h42M19 6v10M41 6v10"/></svg><span>Help<br>scheduling<br>tours</span></div>
  <div class="abs feature" style="left:609px"><svg width="60" height="60" viewBox="0 0 60 60" fill="#8a8a8a"><rect x="12" y="16" width="28" height="24"/><path d="M42 22h8l7 9v9H42z"/><circle cx="20" cy="44" r="5"/><circle cx="48" cy="44" r="5"/><rect x="2" y="20" width="8" height="2.5"/><rect x="4" y="27" width="6" height="2.5"/><rect x="2" y="34" width="8" height="2.5"/></svg><span>Move in<br>support</span></div>
</section>

<section class="advisor" role="img" aria-label="Smiling older man in a striped shirt walking outdoors with hiking poles">
  <h2 class="abs heading">Your <b>LOCAL ADVISOR</b> informs.<br>You decide.</h2>
  <p class="abs lead">Lorem Ipsum is simply dummy text of the printing and typesetting industry</p>
  <div class="abs perk" style="top:157px"><svg width="34" height="32" viewBox="0 0 34 32" fill="none" stroke="#fff" stroke-width="2"><path d="M2 6l9-3 11 3 10-3v23l-10 3-11-3-9 3z"/><circle cx="20" cy="13" r="4"/></svg><span>Insider's tips for the<br>area near you</span></div>
  <div class="abs perk" style="top:212px"><svg width="34" height="30" viewBox="0 0 34 30"><path d="M17 28L4 15a7 7 0 0 1 13-9 7 7 0 0 1 13 9z" fill="#fff"/></svg><span>Advice tailored to your<br>unique situation</span></div>
  <div class="abs perk" style="top:268px"><svg width="34" height="26" viewBox="0 0 34 26" fill="#fff"><rect x="2" y="2" width="4" height="3"/><rect x="9" y="2" width="23" height="3"/><rect x="2" y="9" width="4" height="3"/><rect x="9" y="9" width="23" height="3"/><rect x="2" y="16" width="4" height="3"/><rect x="9" y="16" width="23" height="3"/><rect x="2" y="22" width="4" height="3"/><rect x="9" y="22" width="23" height="3"/></svg><span>Time saving know-how<br>and resources</span></div>
  <div class="abs search-input"><svg width="9" height="12" viewBox="0 0 10 14"><path d="M5 0a5 5 0 0 0-5 5c0 4 5 9 5 9s5-5 5-9a5 5 0 0 0-5-5zm0 7a2 2 0 1 1 0-4 2 2 0 0 1 0 4z" fill="#3a3a3a"/></svg>ENTER CITY OR POSTAL CODE</div>
  <div class="abs btn">Search</div>
</section>

<section class="testimonials">
  <h2 class="heading">Customer Testimonials</h2>
  <div class="abs review" style="left:140px"><div class="portrait" role="img" aria-label="Portrait of a smiling older man in a dark jacket"></div><q>Lorem ipsum is simply<br>dummy text of the.</q><p>Contrary to popular belief, Lorem<br>Ipsum is not simply random text.<br>It has roots in a piece .</p></div>
  <div class="abs review" style="left:379px"><div class="portrait" role="img" aria-label="Portrait of an older man with glasses and a grey vest"></div><q>Lorem ipsum is simply<br>dummy text of the.</q><p>Contrary to popular belief, Lorem<br>Ipsum is not simply random text.<br>It has roots in a piece .</p></div>
  <div class="abs review" style="left:633px"><div class="portrait" role="img" aria-label="Portrait of a smiling older man in a vest and tie"></div><q>Lorem ipsum is simply<br>dummy text of the.</q><p>Contrary to popular belief, Lorem<br>Ipsum is not simply random text.<br>It has roots in a piece .</p></div>
  <div class="abs btn">See more testimonials</div>
</section>

<section class="veterans" role="img" aria-label="Veteran in a cap saluting in front of a national flag">
  <h2 class="abs heading">Access up to<br>$2,000 per month<br>in veteran's aid</h2>
  <p class="abs">Sed ut perspiciatis unde omnis iste natus error sit voluptatem accusantium doloremque laudantium.</p>
  <div class="abs btn">Learn more</div>
</section>

<section class="states">
  <h2 class="heading">Senior Living by State</h2>
  <div class="abs tabs"><span class="active">Assisted Living</span><span>Memory Care</span><span>Independent Living</span><span>Nursing Home</span><span>Care Homes</span></div>
  <div class="abs panel">
    <ul style="left:43px"><li>Alabama</li><li>Alaska</li><li>Arkansas</li><li>California</li><li>Colorado</li><li>Connecticut</li><li>Delaware</li><li>District of Columbia</li><li>Florida</li><li>Georgia</li><li>Hawaii</li><li>Idaho</li><li>Illinois</li><li>Indiana</li></ul>
    <ul style="left:228px"><li>Iowa</li><li>Kansas</li><li>Kentucky</li><li>Louisiana</li><li>Maine</li><li>Maryland</li><li>Massachusetts</li><li>Michigan</li><li>Minnesota</li><li>Mississippi</li><li>Missouri</li><li>Montana</li><li>Nebraska</li><li>Nevada</li></ul>
    <ul style="left:404px"><li>New Hampshire</li><li>New Jersey</li><li>New Mexico</li><li>New York</li><li>North Carolina</li><li>North Dakota</li><li>Ohio</li><li>Oklahoma</li><li>Oregon</li><li>Pennsylvania</li><li>Rhode Island</li><li>South Carolina</li><li>South Dakota</li><li>Tennessee</li></ul>
    <ul style="left:591px"><li>Texas</li><li>Utah</li><li>Vermont</li><li>Virginia</li><li>Washington</li><li>West Virginia</li><li>Wisconsin</li></ul>
  </div>
</section>

<footer class="site-footer">
  <div class="abs footer-brand">The Elder Nook</div>
  <div class="abs follow">FOLLOW US</div>
  <div class="abs social" style="left:148px;background:#3b5aa6"></div>
  <div class="abs social" style="left:184px;background:#1da1f2"></div>
  <div class="abs social" style="left:219px;background:#1b3f8f"></div>
  <div class="abs footer-col about"><h3>About Us</h3><p>But I must explain to you how all this mistaken idea of denouncing pleasure and praising pain was born and I will give you a complete account of the system, and expound the actual teachings of the great.</p></div>
  <div class="abs footer-col menu"><h3>Menu</h3><ul><li>Assisted Living</li><li>Memory Care</li><li>Nursing Homes</li><li>Planning &amp; Advice</li><li>How It Works</li><li>Contact Us</li></ul></div>
</footer>
<div class="abs legal" style="left:0;width:764px">Copyrights @ 2019 All Rights Reserved</div>

</div>
</body>
</html>
```